Web Design Project for SEARCH ENGINE !

We need a website design for torrents search engine.

The Website will be www.Qentrova.com

Qentrova is a a search engine for torrents.
Qentrova search and index torrents results from all torrents sites.

We will need:
Logo
WebSite Design
slogen (optional)

we need only PSDs - no codded pages are needed !

Design to the following screen Size & resolution: 1024 x 768

***PLEASE DOWNLOAD ATTACHED FILE !

```html
<!DOCTYPE html>
<html lang="en">
<head>
<meta charset="utf-8">
<title>Qentrova – Torrents Search Engine</title>
<link rel="stylesheet" href="https://fonts.googleapis.com/css2?family=Questrial&family=Arimo:wght@400;700&family=Open+Sans:wght@400;600&display=swap">
<style>
:root{
  --ink:#4a4a4a;
  --ink-soft:#8a8a8a;
  --bar-dark:#1c1c1c;
  --bar-mid:#2e2e2e;
  --accent-green:#2bb34a;
  --accent-red:#d4202a;
  --accent-orange:#f08a24;
  --peer-blue:#1aa3e0;
  --seed-green:#7cc242;
  --panel:#e6e6e6;
  --panel-dark:#c9c9c9;
  --rule:#a9a9a9;
  --icon-grey:#9aa5b0;
}
*{box-sizing:border-box;margin:0;padding:0}
html,body{width:1200px;height:950px;overflow:hidden}
body{
  position:relative;
  background:linear-gradient(#fff 0,#fff 620px,#e2e2e2 950px);
  font-family:"Open Sans",Arial,sans-serif;color:var(--ink);
}
.top-band{position:absolute;left:0;top:14px;width:1200px;height:48px;background:linear-gradient(#f2f2f2,#dcdcdc)}
.cap{position:absolute;width:18px;height:14px;background:var(--bar-dark);border-radius:0 0 9px 9px}
.cap.bottom{border-radius:9px 9px 0 0}
.nav-bar{position:absolute;left:180px;top:6px;width:840px;height:64px;
  background:linear-gradient(var(--bar-mid),var(--bar-dark));border-radius:0 0 12px 12px;
  box-shadow:0 3px 6px rgba(0,0,0,.35);
  display:flex;align-items:center;padding-left:27px;
  font-family:"Questrial",sans-serif;font-size:15.5px;color:#fff;white-space:nowrap}
.nav-bar a{color:#fff;text-decoration:none}
.nav-bar a.active{color:var(--accent-green)}
.nav-bar .sep{margin:0 10px}
.social{position:absolute;top:31px;width:22px;height:22px;border-radius:4px;background:var(--icon-grey)}
.lang{position:absolute;left:920px;top:23px;width:82px;height:26px;background:var(--accent-green);
  color:#fff;font-size:14px;display:flex;align-items:center;justify-content:center;gap:10px}
.brand{position:absolute;left:22px;top:88px;display:flex;align-items:center;gap:5px}
.brand-dot{width:26px;height:26px;border-radius:50%;background:var(--accent-green)}
.brand-name{font-family:"Arimo",sans-serif;font-weight:700;font-size:25px;color:#6b6b6b;letter-spacing:-.5px}
.brand-tagline{position:absolute;left:23px;top:123px;font-size:9.5px;color:#555;letter-spacing:.1px;white-space:nowrap}
.search{position:absolute;left:180px;top:96px;width:840px;height:38px;background:var(--panel);display:flex}
.search-input{flex:1;font-family:"Arimo",sans-serif;font-size:21px;color:#333;padding:6px 10px}
.search-btn{width:76px;background:var(--bar-dark);color:#fff;font-size:12px;display:flex;align-items:center;justify-content:center;gap:4px}
.result-count{position:absolute;left:180px;top:139px;font-size:12px}
.site-toggle{position:absolute;right:180px;top:139px;font-size:12px;display:flex;align-items:center;gap:4px}
.site-toggle i{display:inline-block;width:13px;height:13px;border:1px solid #888;background:#eee}
.info-bar{position:absolute;left:180px;top:172px;width:840px;height:27px;background:var(--panel);font-size:12.5px;
  display:flex;align-items:center;padding:0 16px;justify-content:space-between;white-space:nowrap}
.info-bar .active,.filter-bar .active{color:var(--accent-red)}
.pager{position:absolute;left:486px;top:168px;width:226px;height:24px;background:var(--bar-dark);border-radius:6px;
  color:#fff;font-size:12.5px;display:flex;align-items:center;justify-content:center;gap:6px}
.pager .current{color:var(--accent-green)}
.filter-bar{position:absolute;left:180px;top:199px;width:840px;height:25px;background:var(--panel-dark);font-size:12.5px;
  display:flex;align-items:center;justify-content:center;gap:40px;white-space:nowrap}
.results{position:absolute;left:180px;top:240px;width:840px;list-style:none}
.result{position:relative;height:44px;border-bottom:1px solid var(--rule);font-size:12.5px;color:var(--ink-soft);white-space:nowrap}
.result .title{position:absolute;left:0;top:17px;font-family:"Arimo",sans-serif;font-size:16px;color:#555}
.result svg{position:absolute;left:544px;top:19px}
.result .date{position:absolute;left:573px;top:18px}
.result .size{position:absolute;left:653px;top:18px}
.badge{position:absolute;top:18px;width:17px;height:17px;color:#fff;font-size:12px;font-weight:600;text-align:center;line-height:17px}
.badge.peers{left:708px;background:var(--peer-blue)}
.badge.seeds{left:784px;background:var(--seed-green)}
.result .pv{position:absolute;left:728px;top:18px}
.result .sv{position:absolute;left:803px;top:18px}
.footer{position:absolute;left:180px;top:879px;width:840px;height:71px;background:linear-gradient(var(--bar-mid),var(--bar-dark));
  border-radius:12px 12px 0 0;box-shadow:0 -3px 6px rgba(0,0,0,.3);
  font-family:"Questrial",sans-serif;font-size:13.5px;color:#fff;text-align:center;line-height:62px;white-space:nowrap;padding-top:4px}
.footer a{color:var(--accent-green);text-decoration:none}
</style>
</head>
<body>
<div class="top-band"></div>
<span class="cap" style="left:158px;top:6px"></span>
<span class="cap" style="left:1024px;top:6px"></span>

<span class="social" style="left:12px"></span>
<span class="social" style="left:56px"></span>
<span class="social" style="left:100px"></span>
<span class="social" style="left:144px"></span>

<nav class="nav-bar">
  <a class="active" href="#">HOME</a><span class="sep">|</span>
  <a href="#">ABOUT US</a><span class="sep">|</span>
  <a href="#">TORRENT SEARCH</a><span class="sep">|</span>
  <a href="#">SITE SEARCH</a><span class="sep">|</span>
  <a href="#">HELP</a><span class="sep">|</span>
  <a href="#">LOGIN</a><span class="sep">|</span>
  <a href="#">SIGNIN</a>
</nav>
<div class="lang">English <span>▼</span></div>

<span class="social" style="left:1034px"></span>
<span class="social" style="left:1077px"></span>
<span class="social" style="left:1121px"></span>
<span class="social" style="left:1164px"></span>

<div class="brand"><span class="brand-dot"></span><span class="brand-name">Qentrova</span></div>
<div class="brand-tagline">TORRENTS SEARCH ENGINE</div>

<div class="search">
  <div class="search-input">skyforgers 3</div>
  <div class="search-btn">
    <svg width="11" height="11" viewBox="0 0 11 11"><circle cx="4.5" cy="4.5" r="3.3" fill="none" stroke="#fff" stroke-width="1.6"/><line x1="7" y1="7" x2="10" y2="10" stroke="#fff" stroke-width="1.8"/></svg>SEARCH
  </div>
</div>
<div class="result-count">About 50,000 results (0.12 seconds)</div>
<div class="site-toggle">Sites search include <i></i></div>

<div class="info-bar">
  <span>1 - 10 of 20 for “ skyforgers 3 ” ( 1,155s )</span>
  <span>Order by : | <span class="active">name</span> | date | size | peers | seeds</span>
</div>
<div class="pager">previous | 1 | 2 | <span class="current">3</span> | 4 | next</div>
<div class="filter-bar">
  <span>Quality : | <span class="active">all</span> | good | bad | verified</span>
  <span>Search by : | filename | <span class="active">titles</span> | data added</span>
</div>

<ul class="results">
  <li class="result"><span class="title">skyforgers 3&nbsp; HD QVR kvrtlmn.225</span><svg width="16" height="16" viewBox="0 0 16 16"><circle cx="8" cy="8" r="6.5" fill="none" stroke="#2bb34a" stroke-width="2"/><path d="M5 8h6M8 5v6" stroke="#2bb34a" stroke-width="2"/></svg><span class="date">3 days ago</span><span class="size">549 MB</span><span class="badge peers">P</span><span class="pv">10.555</span><span class="badge seeds">S</span><span class="sv">10.200</span></li>
  <li class="result"><span class="title">skyforgers 3&nbsp; HD QVR kvrtlmn.225</span><svg width="16" height="16" viewBox="0 0 16 16"><circle cx="8" cy="8" r="6.5" fill="none" stroke="#d4202a" stroke-width="2"/><path d="M5 8h6" stroke="#d4202a" stroke-width="2"/></svg><span class="date">3 days ago</span><span class="size">549 MB</span><span class="badge peers">P</span><span class="pv">10.555</span><span class="badge seeds">S</span><span class="sv">10.200</span></li>
  <li class="result"><span class="title">skyforgers 3&nbsp; HD QVR kvrtlmn.225</span><svg width="16" height="16" viewBox="0 0 16 16"><circle cx="8" cy="8" r="6.5" fill="none" stroke="#2bb34a" stroke-width="2"/><path d="M5 8h6M8 5v6" stroke="#2bb34a" stroke-width="2"/></svg><span class="date">3 days ago</span><span class="size">549 MB</span><span class="badge peers">P</span><span class="pv">10.555</span><span class="badge seeds">S</span><span class="sv">10.200</span></li>
  <li class="result"><span class="title">skyforgers 3&nbsp; HD QVR kvrtlmn.225</span><svg width="16" height="16" viewBox="0 0 16 16"><circle cx="8" cy="8" r="6.5" fill="none" stroke="#2bb34a" stroke-width="2"/><path d="M5 8h6M8 5v6" stroke="#2bb34a" stroke-width="2"/></svg><span class="date">3 days ago</span><span class="size">549 MB</span><span class="badge peers">P</span><span class="pv">10.555</span><span class="badge seeds">S</span><span class="sv">10.200</span></li>
  <li class="result"><span class="title">skyforgers 3&nbsp; HD QVR kvrtlmn.225</span><svg width="16" height="16" viewBox="0 0 16 16"><circle cx="8" cy="8" r="6.5" fill="none" stroke="#d4202a" stroke-width="2"/><path d="M5 8h6" stroke="#d4202a" stroke-width="2"/></svg><span class="date">3 days ago</span><span class="size">549 MB</span><span class="badge peers">P</span><span class="pv">10.555</span><span class="badge seeds">S</span><span class="sv">10.200</span></li>
  <li class="result"><span class="title">skyforgers 3&nbsp; HD QVR kvrtlmn.225</span><svg width="16" height="16" viewBox="0 0 16 16"><circle cx="8" cy="8" r="6.5" fill="none" stroke="#f08a24" stroke-width="2"/><circle cx="8" cy="8" r="2.8" fill="#f08a24"/></svg><span class="date">3 days ago</span><span class="size">549 MB</span><span class="badge peers">P</span><span class="pv">10.555</span><span class="badge seeds">S</span><span class="sv">10.200</span></li>
  <li class="result"><span class="title">skyforgers 3&nbsp; HD QVR kvrtlmn.225</span><svg width="16" height="16" viewBox="0 0 16 16"><circle cx="8" cy="8" r="6.5" fill="none" stroke="#2bb34a" stroke-width="2"/><path d="M5 8h6M8 5v6" stroke="#2bb34a" stroke-width="2"/></svg><span class="date">3 days ago</span><span class="size">549 MB</span><span class="badge peers">P</span><span class="pv">10.555</span><span class="badge seeds">S</span><span class="sv">10.200</span></li>
  <li class="result"><span class="title">skyforgers 3&nbsp; HD QVR kvrtlmn.225</span><svg width="16" height="16" viewBox="0 0 16 16"><circle cx="8" cy="8" r="6.5" fill="none" stroke="#2bb34a" stroke-width="2"/><path d="M5 8h6M8 5v6" stroke="#2bb34a" stroke-width="2"/></svg><span class="date">3 days ago</span><span class="size">549 MB</span><span class="badge peers">P</span><span class="pv">10.555</span><span class="badge seeds">S</span><span class="sv">10.200</span></li>
  <li class="result"><span class="title">skyforgers 3&nbsp; HD QVR kvrtlmn.225</span><svg width="16" height="16" viewBox="0 0 16 16"><circle cx="8" cy="8" r="6.5" fill="none" stroke="#f08a24" stroke-width="2"/><circle cx="8" cy="8" r="2.8" fill="#f08a24"/></svg><span class="date">3 days ago</span><span class="size">549 MB</span><span class="badge peers">P</span><span class="pv">10.555</span><span class="badge seeds">S</span><span class="sv">10.200</span></li>
  <li class="result"><span class="title">skyforgers 3&nbsp; HD QVR kvrtlmn.225</span><svg width="16" height="16" viewBox="0 0 16 16"><circle cx="8" cy="8" r="6.5" fill="none" stroke="#d4202a" stroke-width="2"/><path d="M5 8h6" stroke="#d4202a" stroke-width="2"/></svg><span class="date">3 days ago</span><span class="size">549 MB</span><span class="badge peers">P</span><span class="pv">10.555</span><span class="badge seeds">S</span><span class="sv">10.200</span></li>
  <li class="result"><span class="title">skyforgers 3&nbsp; HD QVR kvrtlmn.225</span><svg width="16" height="16" viewBox="0 0 16 16"><circle cx="8" cy="8" r="6.5" fill="none" stroke="#f08a24" stroke-width="2"/><circle cx="8" cy="8" r="2.8" fill="#f08a24"/></svg><span class="date">3 days ago</span><span class="size">549 MB</span><span class="badge peers">P</span><span class="pv">10.555</span><span class="badge seeds">S</span><span class="sv">10.200</span></li>
  <li class="result"><span class="title">skyforgers 3&nbsp; HD QVR kvrtlmn.225</span><svg width="16" height="16" viewBox="0 0 16 16"><circle cx="8" cy="8" r="6.5" fill="none" stroke="#2bb34a" stroke-width="2"/><path d="M5 8h6M8 5v6" stroke="#2bb34a" stroke-width="2"/></svg><span class="date">3 days ago</span><span class="size">549 MB</span><span class="badge peers">P</span><span class="pv">10.555</span><span class="badge seeds">S</span><span class="sv">10.200</span></li>
  <li class="result"><span class="title">skyforgers 3&nbsp; HD QVR kvrtlmn.225</span><svg width="16" height="16" viewBox="0 0 16 16"><circle cx="8" cy="8" r="6.5" fill="none" stroke="#2bb34a" stroke-width="2"/><path d="M5 8h6M8 5v6" stroke="#2bb34a" stroke-width="2"/></svg><span class="date">3 days ago</span><span class="size">549 MB</span><span class="badge peers">P</span><span class="pv">10.555</span><span class="badge seeds">S</span><span class="sv">10.200</span></li>
</ul>

<footer class="footer">COPYRIGHT © 2011 QENTROVA. USE OF THIS WEBSITE CONSTITUTES ACCEPTANCE OF OUR <a href="#">USER AGREEMENT</a> AND <a href="#">PRIVACY POLICY</a>.</footer>
<span class="cap bottom" style="left:158px;top:936px"></span>
<span class="cap bottom" style="left:1024px;top:936px"></span>
</body>
</html>
```